Home Page Design

We are refreshing our website and need someone to design a very clean modern home page. We have a wireframe for the content and basic layout (see attached). We just need someone to make it look beautiful.

This web page will be hosted on a private server using HTML5. I have developers who will integrate the rotating images and referenced video files - we just need you to focus on the visual elements.

You can take a look at our current website at fennawicks.com for color style guides, logos, etc.

```html
<!DOCTYPE html>
<html lang="en">
<head>
<meta charset="utf-8">
<title>Fennawicks – Home</title>
<link rel="stylesheet" href="https://fonts.googleapis.com/css2?family=Inter:wght@300;400&display=swap">
<style>
  :root {
    --brand-blue: #1f5fad;
    --footer-navy: #1a3553;
    --star-orange: #f6a623;
    --cta-green: #76c942;
    --ink: #1f1f1f;
    --ink-soft: #3a3a3a;
    --white: #ffffff;
    --photo-warm: #c9bfb3;
    --photo-cool: #6f7a86;
  }
  * { box-sizing: border-box; margin: 0; padding: 0; }
  html, body { width: 1200px; height: 1200px; overflow: hidden; }
  body {
    position: relative;
    background: var(--white);
    font-family: "Inter", "Helvetica Neue", Arial, sans-serif;
    color: var(--ink);
  }
  .testimonial {
    position: absolute; left: 0; top: 0; width: 1200px; height: 392px;
    background: var(--brand-blue); color: var(--white);
  }
  .testimonial__quote {
    position: absolute; left: 132px; top: 28px; width: 440px;
    font-size: 14.4px; font-weight: 300; line-height: 27.5px; letter-spacing: -0.1px;
  }
  .testimonial__author {
    position: absolute; left: 134px; top: 190px;
    font-size: 18.5px; font-weight: 300; line-height: 23px;
  }
  .testimonial__stars { position: absolute; left: 131px; top: 245px; }
  .photo {
    position: absolute; left: 618px; width: 495px;
  }
  .photo--meeting {
    top: 0; height: 298px;
    background: linear-gradient(135deg, #e9e6e2 0%, var(--photo-warm) 45%, #3a4150 70%, #f0eeeb 100%);
  }
  .photo--team {
    top: 489px; height: 330px;
    background: linear-gradient(120deg, var(--photo-cool) 0%, #b9b3ab 45%, #2b3d6e 80%, #d8d3cc 100%);
  }
  .assessment__title {
    position: absolute; left: 133px; top: 482px;
    font-size: 32px; font-weight: 300; color: var(--ink);
  }
  .assessment__subtitle {
    position: absolute; left: 133px; top: 526px;
    font-size: 22px; font-weight: 300; color: var(--ink);
  }
  .assessment__body {
    position: absolute; left: 134px; top: 585px; width: 470px;
    font-size: 14.4px; font-weight: 300; line-height: 27.5px; color: var(--ink-soft);
  }
  .button-cta {
    position: absolute; left: 133px; top: 776px; width: 130px; height: 35px;
    background: var(--cta-green); color: var(--white); border-radius: 4px;
    font-size: 12.5px; font-weight: 400; line-height: 35px; text-align: center;
  }
  .site-footer {
    position: absolute; left: 0; top: 912px; width: 1200px; height: 288px;
    background: var(--footer-navy); color: var(--white);
    font-size: 11.5px; font-weight: 400;
  }
  .site-footer a, .site-footer span { position: absolute; color: var(--white); text-decoration: none; white-space: nowrap; }
  .social-dot { width: 11px; height: 11px; border-radius: 50%; background: var(--white); position: absolute; }
</style>
</head>
<body>
  <section class="testimonial">
    <p class="testimonial__quote">“We knew we had a problem with skyrocketing Skyforge costs, but did not know how to fix it. These guys are complete professionals and know exactly what they are doing. Within just a few short months Fennawicks reduced my monthly Skyforge bill by over 60% and I could not be happier!”</p>
    <p class="testimonial__author">Marta Ellison<br>Cloud Engineer</p>
    <svg class="testimonial__stars" width="130" height="28" viewBox="0 0 130 28" aria-label="Five star rating">
      <g fill="none" stroke="var(--star-orange)" stroke-width="4" stroke-linecap="round">
        <g id="star"><path d="M13 2v24M2 8l22 12M2 20L24 8"/></g>
        <use href="#star" x="26"/><use href="#star" x="52"/><use href="#star" x="78"/><use href="#star" x="104"/>
      </g>
    </svg>
    <div class="photo photo--meeting" role="img" aria-label="Three colleagues shaking hands across an office table"></div>
  </section>

  <section class="assessment">
    <h2 class="assessment__title">Free Assessment</h2>
    <p class="assessment__subtitle">No Risk * Real Cost Savings Estimate</p>
    <p class="assessment__body">Wondering if Fennawicks is a good fit for your organization?<br>Toke the guess work out of it and sign for a free assessment. Our team of cloud analysts will work with you to perform a free assessment of your Skyforge environment, including the specific cost saving opportunities they identified and the potential annual savings.</p>
    <a class="button-cta" href="#">Free Assessment</a>
    <div class="photo photo--team" role="img" aria-label="Smiling team seated along a conference table"></div>
  </section>

  <footer class="site-footer">
    <a style="left:74px;top:30px">Company</a>
    <a style="left:74px;top:56px">About Us</a>
    <a style="left:74px;top:82px">Contact Us</a>

    <a style="left:232px;top:33px">Product</a>
    <a style="left:232px;top:60px">Solutions</a>
    <a style="left:232px;top:90px">Features</a>
    <a style="left:232px;top:115px">Pricing</a>
    <a style="left:232px;top:140px">FAQ</a>

    <a style="left:372px;top:33px">Customer</a>
    <a style="left:372px;top:56px">Sales</a>
    <a style="left:372px;top:79px">Support</a>

    <a style="left:518px;top:33px">Partners</a>
    <a style="left:518px;top:56px">Become a Reseller</a>
    <a style="left:518px;top:80px">Portal Login</a>

    <a style="left:68px;top:236px">Privacy Policy</a>
    <a style="left:148px;top:236px">Terms of Service</a>
    <span style="left:455px;top:238px">(c) 2019 Fennawicks. All Rights Reserved</span>
    <span style="left:888px;top:239px">Follow Us</span>
    <i class="social-dot" style="left:948px;top:241px" aria-label="Social link"></i>
    <i class="social-dot" style="left:970px;top:241px" aria-label="Social link"></i>
    <i class="social-dot" style="left:993px;top:241px" aria-label="Social link"></i>
  </footer>
</body>
</html>
```